Business card - KT Placement Partners / The Danford Group

We need a business card and logo design for my executive search (recruiting / headhunting) firm. We find people to fill open jobs at companies. We are a U.S. based company and do some global work also. So maybe something with a globe but definitely looking for other options also. Maybe something incorporating the letters KT which is our current logo but looking at options. The card should say BOTH full company names and tag line-

KT Placement Partners / The Danford Group
Leadership Hiring Results You Can Rely On

The design should say about the company-
Sharp
Reliable
Find the best people for the job
Business oriented
Results achieved
Modern

Target Market(s)

Business owners, CEO's, and heads of human resources departments

Industry/Entity Type

Business Consultant

Contact Information for Business Card

The card MUST say BOTH full company names and tag line-

Logo Text

Logo does not NEED to say anything on the design itself, but could if designed that way.

Font styles to use
Serif
Sans Serif

Requirements
Must have
• The business cards need to have. In addition to name, title, address, phone, website, and email address,
• The card MUST say BOTH full company names and tag line-
• KT Placement Partners / The Danford Group
• Leadership Hiring Results You Can Rely On
Nice to have
• The design should say about the company-
• Sharp
• Reliable
• Find the best people for the job
• Business oriented
• Results achieved
• Modern
• Maybe something with a globe or the letters KT or relating to people. Open to options.
Should not have
• Should not be cutesy or funny, for this design

```html
<!DOCTYPE html>
<html lang="en">
<head>
<meta charset="utf-8">
<title>KT Placement Partners – Business Card</title>
<link rel="stylesheet" href="https://fonts.googleapis.com/css2?family=Montserrat:wght@300;400;600;700&family=Lato:wght@400;700&display=swap">
<style>
  :root {
    --stage: #2a2a2c;
    --navy: #0f2f5c;
    --navy-light: #1d4478;
    --brand-blue: #174a86;
    --ink: #2b2b2b;
    --paper: #fbfbfb;
    --map-tint: #dcdde8;
    --white: #ffffff;
    --soft-white: #e6ebf3;
  }
  * { margin: 0; padding: 0; box-sizing: border-box; }
  html, body { width: 1200px; height: 873px; overflow: hidden; }
  body {
    background: var(--stage);
    display: flex; flex-direction: column; align-items: center; justify-content: center;
    gap: 56px;
  }
  .card {
    position: relative;
    width: 600px; height: 343px;
    box-shadow: 0 8px 24px rgba(0,0,0,.45);
    overflow: hidden;
  }

  /* Shared lockup */
  .lockup { position: absolute; display: flex; align-items: center; }
  .lockup-mark { width: 26px; height: 26px; margin-right: 18px; flex: none; }
  .lockup-rule { width: 1.5px; align-self: stretch; margin-right: 12px; flex: none; }
  .lockup-names { display: flex; flex-direction: column; }
  .lockup-primary {
    font-family: "Montserrat", sans-serif; font-weight: 300; font-size: 24px; line-height: 1.1;
    white-space: nowrap;
  }
  .lockup-secondary {
    font-family: "Montserrat", sans-serif; font-weight: 700; font-size: 15px;
    letter-spacing: .32em; text-transform: uppercase; margin-top: 2px; white-space: nowrap;
  }

  /* Back side */
  .card-back {
    background: linear-gradient(135deg, var(--navy-light) 0%, var(--navy) 70%);
    color: var(--white);
  }
  .card-back .lockup { left: 120px; top: 128px; }
  .card-back .lockup-mark { background: var(--white); }
  .card-back .lockup-rule { background: var(--white); }
  .card-back .lockup-secondary { color: var(--soft-white); }
  .tagline {
    position: absolute; left: 120px; bottom: 56px;
    font-family: "Montserrat", sans-serif; font-weight: 600; font-size: 13px;
    letter-spacing: .12em; color: var(--soft-white); white-space: nowrap;
  }

  /* Front side */
  .card-front { background: var(--paper); color: var(--ink); }
  .world-map {
    position: absolute; left: 150px; top: 30px; width: 420px; height: 210px;
    background: radial-gradient(ellipse at center, var(--map-tint) 0%, rgba(220,221,232,.4) 60%, rgba(251,251,251,0) 80%);
  }
  .card-front .lockup { left: 40px; top: 42px; }
  .card-front .lockup-mark { background: var(--brand-blue); }
  .card-front .lockup-rule { background: var(--ink); }
  .card-front .lockup-primary { color: #333; font-size: 20px; }
  .card-front .lockup-secondary { color: var(--brand-blue); font-size: 13px; }
  .person { position: absolute; right: 40px; top: 118px; text-align: right; }
  .person-name { font-family: "Lato", sans-serif; font-size: 20px; color: var(--brand-blue); line-height: 1.1; }
  .person-name strong { font-weight: 700; }
  .person-title { font-family: "Lato", sans-serif; font-weight: 700; font-size: 11px; color: var(--ink); }
  .person-rule { position: absolute; right: 40px; top: 164px; width: 190px; height: 2px; background: var(--ink); }
  .contact-rule { position: absolute; left: 40px; top: 196px; width: 300px; height: 2px; background: var(--ink); }
  .address {
    position: absolute; left: 40px; top: 206px;
    font-family: "Lato", sans-serif; font-weight: 700; font-size: 13px; color: var(--brand-blue);
    white-space: nowrap;
  }
  .contact-list { position: absolute; left: 40px; top: 234px; list-style: none; }
  .contact-list li {
    display: flex; align-items: center; gap: 14px;
    font-family: "Lato", sans-serif; font-size: 14px; color: var(--ink); height: 25px;
    white-space: nowrap;
  }
  .contact-list svg { width: 14px; height: 14px; fill: var(--brand-blue); flex: none; }
</style>
</head>
<body>

<section class="card card-back">
  <div class="lockup">
    <span class="lockup-mark"></span>
    <span class="lockup-rule"></span>
    <div class="lockup-names">
      <span class="lockup-primary">KT Placement Partners</span>
      <span class="lockup-secondary">The Danford Group</span>
    </div>
  </div>
  <p class="tagline">Leadership Hiring Results You Can Rely On</p>
</section>

<section class="card card-front">
  <div class="world-map" role="img" aria-label="Dotted world map in light grey and lavender"></div>
  <div class="lockup">
    <span class="lockup-mark"></span>
    <span class="lockup-rule"></span>
    <div class="lockup-names">
      <span class="lockup-primary">KT Placement Partners</span>
      <span class="lockup-secondary">The Danford Group</span>
    </div>
  </div>
  <div class="person">
    <p class="person-name">Marcus <strong>Ellery</strong></p>
    <p class="person-title">Athletic Director</p>
  </div>
  <span class="person-rule"></span>
  <span class="contact-rule"></span>
  <p class="address">48 Alder Court, Brookfield, PA 15020</p>
  <ul class="contact-list">
    <li>
      <svg viewBox="0 0 16 16" aria-hidden="true"><path d="M2 5c0-2 2-3 6-3s6 1 6 3v1h-3V5H5v1H2zM4 7h8l2 7H2z"/></svg>
      555-214-0387
    </li>
    <li>
      <svg viewBox="0 0 16 16" aria-hidden="true"><path d="M4 1h8v4H4zM1 6h14v6h-3v3H4v-3H1zM5 10v4h6v-4z"/></svg>
      555-214-0392
    </li>
    <li>
      <svg viewBox="0 0 16 16" aria-hidden="true"><path d="M1 3h14v10H1zM2 4l6 5 6-5v1l-6 5-6-5z" fill-rule="evenodd"/></svg>
      mjellery@ktplacementpartners
    </li>
  </ul>
</section>

</body>
</html>
```